Meadowrun Acres Website Design

We have been redeveloping our website already and are quite happy with the content, but the design needs to be better:
https://tilvexa-hub.examplehost.net/

Pages, content, concept etc. Can all be taken from the redeveloped website.
The farmer can register and edit/view their profile, subscribe and these pages need to be designed better as well as contact, about, pricing, tos, privacy and a page with example portlets.

We need a website to appeal to farmers, investors and retiring farmers.

The design should be clean and a little country.

We don't want any repeat designs that some may submit to every project and has no respect for the project brief, so please don't submit them.

Target Market(s)

farmers, investors, retirees

Industry/Entity Type

Farming

Number of Pages Required

5+ page

Colors

Designer to choose colors to be used in the design.

Requirements
Must have
• Nice, clean modern design that is appealing
• Profile page laid out nicely

```html
<!DOCTYPE html>
<html lang="en">
<head>
<meta charset="utf-8">
<title>Meadowrun Acres</title>
<link rel="stylesheet" href="https://fonts.googleapis.com/css2?family=Montserrat:wght@400;500;600;700&family=Open+Sans:wght@400;600;700&display=swap">
<style>
:root{
  --green:#3aaa35;
  --green-dark:#1f7a2c;
  --green-deep:#2b8a31;
  --ink:#333;
  --muted:#555;
  --card:#efefef;
  --disc:#ececec;
  --footer:#f3f3f3;
  --bar:#e6e6e6;
  --white:#fff;
}
*{box-sizing:border-box;margin:0;padding:0}
html,body{width:1200px;height:2961px;overflow:hidden}
body{position:relative;background:var(--white);font-family:"Open Sans",Arial,sans-serif;color:var(--ink)}
.abs{position:absolute}
/* header */
.topline{left:0;top:0;width:1200px;height:4px;background:var(--green)}
.header{left:0;top:4px;width:1200px;height:114px}
.brand{left:116px;top:40px;display:flex;align-items:center;gap:12px;font-family:"Montserrat",sans-serif;font-weight:600;font-size:26px;color:var(--green)}
.brand .dot{width:20px;height:20px;border-radius:50%;background:var(--green)}
.nav{left:416px;top:46px;display:flex;align-items:center;gap:38px;font-family:"Montserrat",sans-serif;font-size:14px;color:#444}
.nav .btn{color:#fff;font-weight:600;padding:5px 12px;border-radius:2px}
.nav .pricing{background:var(--green);margin-left:-10px}
.nav .login{background:var(--green-dark);margin-left:-24px}
/* hero */
.hero{left:0;top:118px;width:1200px;height:553px;background:linear-gradient(160deg,#7b8a5a 0%,#a9a27a 35%,#6e7f4a 65%,#9c9a76 100%)}
.profile{left:103px;top:369px;width:365px;height:164px;background:rgba(255,255,255,.9);padding:18px 22px}
.profile h2{font-family:"Montserrat",sans-serif;font-weight:500;font-size:21px;color:var(--green);margin-bottom:10px}
.profile p{font-size:11.5px;line-height:19px;color:#333}
.profile .view{display:inline-block;margin-top:10px;background:var(--green-deep);color:#fff;font-size:11px;font-weight:600;padding:4px 12px}
.dots{left:1063px;top:466px;display:flex;flex-direction:column;gap:12px}
.dots span{width:17px;height:17px;border-radius:50%;background:#111}
.dots span.on{background:var(--green)}
/* audience cards */
.card{top:578px;width:312px;height:488px;background:var(--card)}
.card h3{height:93px;background:var(--green);color:#fff;font-family:"Montserrat",sans-serif;font-weight:500;font-size:26px;text-align:center;line-height:93px}
.card .icon{display:block;width:100px;height:100px;margin:22px auto 0}
.card .body{padding:28px 26px 0;text-align:center;font-size:12.5px;line-height:20px;color:#444}
.card .actions{position:absolute;left:0;right:0;bottom:18px;display:flex;justify-content:center;align-items:center;gap:18px;font-size:13px}
.card .b{background:var(--green-deep);color:#fff;font-family:"Montserrat",sans-serif;font-weight:600;font-size:12.5px;padding:8px 18px;border-radius:2px}
.card .b.light{background:var(--green)}
.card .b.dark{background:var(--green-dark)}
.signup{left:0;top:1096px;width:1200px;text-align:center;font-size:12.5px;font-weight:600;color:#222}
.signup span{color:var(--green)}
/* video band */
.video{left:0;top:1145px;width:1200px;height:474px;background:linear-gradient(100deg,#4a4540 0%,#6a4a3c 40%,#5c3c34 60%,#3f3a36 100%)}
.play{left:561px;top:1351px}
.video-title{left:0;top:1440px;width:1200px;text-align:center;color:#fff;font-family:"Montserrat",sans-serif;font-weight:600;font-size:40px}
.video-sub{left:0;top:1494px;width:1200px;text-align:center;color:#eee;font-size:13px}
/* steps */
.steps-title{left:0;top:1656px;width:1200px;text-align:center;font-family:"Montserrat",sans-serif;font-weight:400;font-size:32px;color:var(--green)}
.step{top:1750px;width:280px;text-align:center}
.step .ring{position:relative;width:212px;height:212px;margin:0 auto;border:3px dashed var(--green);border-radius:50%;padding:8px}
.step .disc{width:100%;height:100%;border-radius:50%;background:var(--disc);display:flex;align-items:center;justify-content:center}
.step .num{position:absolute;left:16px;top:-4px;width:44px;height:44px;border-radius:50%;background:var(--green);color:#fff;font-family:"Montserrat",sans-serif;font-weight:600;font-size:19px;line-height:44px;text-align:center}
.step p{margin-top:22px;font-family:"Montserrat",sans-serif;font-weight:600;font-size:15px;line-height:22px;color:var(--green)}
.step .b{display:inline-block;margin-top:14px;width:136px;background:var(--green-deep);color:#fff;font-family:"Montserrat",sans-serif;font-weight:600;font-size:13px;padding:8px 0;border-radius:2px}
/* testimonials */
.testimonials{left:0;top:2158px;width:1200px;height:501px;background:linear-gradient(180deg,#5aa86a 0%,#4c9a58 45%,#3c8a45 100%)}
.testi-title{left:0;top:2228px;width:1200px;text-align:center;color:#fff;font-family:"Montserrat",sans-serif;font-weight:600;font-size:28px}
.quote{top:2331px;width:392px;height:127px;background:#fff;padding:18px 22px;font-size:12.5px;line-height:22px;color:#444}
.quote::after{content:"";position:absolute;left:58px;bottom:-14px;border-left:14px solid transparent;border-right:14px solid transparent;border-top:14px solid #fff}
.author{top:2496px;display:flex;align-items:center;gap:12px;color:#fff;font-size:13px}
.author .avatar{width:50px;height:50px;border-radius:50%;background:#e6c9b0;border:3px solid #fff}
.tdots{left:575px;top:2605px;display:flex;gap:10px}
.tdots span{width:10px;height:10px;border-radius:50%;background:#fff}
/* footer */
.footer{left:0;top:2659px;width:1200px;height:263px;background:var(--footer)}
.fcol h4{font-family:"Montserrat",sans-serif;font-weight:500;font-size:23px;color:#333;margin-bottom:22px}
.links li{list-style:none;font-size:12.5px;color:#444;line-height:26px;padding-left:26px;position:relative}
.links li::before{content:"";position:absolute;left:4px;top:9px;border-top:4px solid transparent;border-bottom:4px solid transparent;border-left:5px solid #444}
.email{width:188px;height:28px;border:1px solid #ccc;background:#fff;font-size:11px;color:#666;padding:6px 10px}
.subscribe{display:inline-block;margin-top:14px;background:var(--green-deep);color:#fff;font-size:12px;padding:6px 20px;border-radius:4px}
.contact li{list-style:none;display:flex;gap:14px;font-size:12.5px;color:#333;line-height:21px;margin-bottom:16px}
.social{display:flex;gap:8px}
.social span{width:30px;height:30px;border-radius:50%;background:var(--green)}
.fbrand{left:862px;top:2838px;display:flex;align-items:center;gap:10px;font-family:"Montserrat",sans-serif;font-weight:600;font-size:17px;color:var(--green)}
.fbrand .dot{width:14px;height:14px;border-radius:50%;background:var(--green)}
.copyright{left:0;top:2922px;width:1200px;height:39px;background:var(--bar);text-align:center;line-height:39px;font-size:11.5px;color:#333}
</style>
</head>
<body>
<div class="abs topline"></div>
<header class="abs header">
  <div class="abs brand"><span class="dot"></span>Meadowrun Acres</div>
  <nav class="abs nav">
    <span>Home</span><span>Aspiring Farmers</span><span>Investors</span><span>Retiring Farmer</span><span>Blog</span>
    <span class="btn pricing">Pricing</span><span class="btn login">Login</span>
  </nav>
</header>

<section class="abs hero" role="img" aria-label="Photo of a young farming family and an older farmer seated outdoors among trees"></section>
<div class="abs profile">
  <h2>Tomas Hartley &amp; ewew adsf</h2>
  <p>I really love to farm as farming is forever. I would love to farm anywhere there is an opportunity to live and work in a local farming community.</p>
  <span class="view">View Profile</span>
</div>
<div class="abs dots"><span></span><span class="on"></span><span></span></div>

<article class="abs card" style="left:99px">
  <h3>Farmers</h3>
  <svg class="icon" viewBox="0 0 100 100" role="img" aria-label="Wheat icon">
    <g fill="var(--green)">
      <g id="stalk">
        <rect x="48.5" y="30" width="3" height="64"/>
        <ellipse cx="50" cy="14" rx="3.5" ry="8"/>
        <ellipse cx="43" cy="28" rx="4" ry="8" transform="rotate(-35 43 28)"/>
        <ellipse cx="57" cy="28" rx="4" ry="8" transform="rotate(35 57 28)"/>
        <ellipse cx="43" cy="44" rx="4" ry="8" transform="rotate(-35 43 44)"/>
        <ellipse cx="57" cy="44" rx="4" ry="8" transform="rotate(35 57 44)"/>
        <ellipse cx="43" cy="60" rx="4" ry="8" transform="rotate(-35 43 60)"/>
        <ellipse cx="57" cy="60" rx="4" ry="8" transform="rotate(35 57 60)"/>
      </g>
      <use href="#stalk" x="-28" y="6"/>
      <use href="#stalk" x="28" y="6"/>
    </g>
  </svg>
  <div class="body">Register as an Aspiring Farmer<br><br>Free Fieldmark market analysis membership<br>(valued at $300 pa)<br>Farm business webinars (valued at $200)<br>Corporate Partner Opportunities<br>Public or Private profile (as required)<br>Eligible to enter competitions and win prizes</div>
  <div class="actions"><span class="b">Join Now</span></div>
</article>
<article class="abs card" style="left:444px">
  <h3>Investors</h3>
  <svg class="icon" viewBox="0 0 100 100" role="img" aria-label="Hand holding a growing dollar sprout icon">
    <g fill="var(--green)">
      <text x="50" y="26" text-anchor="middle" font-family="Montserrat, sans-serif" font-weight="700" font-size="26">$</text>
      <rect x="48.5" y="30" width="3" height="36"/>
      <path d="M50 52 C40 52 33 46 31 38 C41 38 48 43 50 52 Z"/>
      <path d="M50 46 C60 46 67 40 69 32 C59 32 52 37 50 46 Z"/>
      <path d="M8 70 L24 64 C30 62 36 62 42 64 L56 68 C61 69 61 75 56 76 L42 76 L58 78 L80 66 C85 63 90 68 86 72 L64 88 C60 91 55 92 50 91 L8 86 Z"/>
    </g>
  </svg>
  <div class="body">We have the best farmers in Australia ready to work with you on your farm.<br>Simply browse the list and decide who you want to work with. No registration required and your information will be kept private.</div>
  <div class="actions"><span class="b light">Sign Up Now</span>Or<span class="b dark">Find out More</span></div>
</article>
<article class="abs card" style="left:790px">
  <h3>Retiring farmers</h3>
  <svg class="icon" viewBox="0 0 100 100" role="img" aria-label="Two people silhouette icon">
    <g fill="var(--green)">
      <circle cx="32" cy="14" r="8"/>
      <path d="M24 26 H40 L50 62 H38 V94 H33 V62 H31 V94 H26 V62 H14 Z"/>
      <circle cx="66" cy="14" r="8"/>
      <path d="M57 26 H75 C78 26 80 28 80 31 V60 H74 V94 H68 V62 H64 V94 H58 V60 H52 V31 C52 28 54 26 57 26 Z"/>
      <path d="M82 46 C82 40 90 40 90 46 V94 H87 V46 C87 44 85 44 85 46 Z"/>
    </g>
  </svg>
  <div class="body">Are you looking for a positive way to step back from your farm?<br>We can connect you with a passionate aspiring farming family who will love your farm just as much as you do. No registration required and your information will be kept private</div>
  <div class="actions"><span class="b light">Enquire Now</span>Or<span class="b dark">Find out More</span></div>
</article>
<p class="abs signup">By <span>signing up now</span>, you will help us get you farm-ready and to find your dream farm.</p>

<section class="abs video" role="img" aria-label="Photo of a farmer hugging two children and a puppy beside a shed"></section>
<svg class="abs play" width="78" height="78" viewBox="0 0 78 78"><circle cx="39" cy="39" r="36" fill="none" stroke="#fff" stroke-width="3"/><path d="M32 25 L54 39 L32 53 Z" fill="#fff"/></svg>
<h2 class="abs video-title">Farm Ownership</h2>
<p class="abs video-sub">It's time to realise your farming dream.</p>

<h2 class="abs steps-title">Aspiring Farmers</h2>
<div class="abs step" style="left:170px">
  <div class="ring"><div class="disc">
    <svg width="90" height="90" viewBox="0 0 90 90" role="img" aria-label="Person in a hat icon" fill="none" stroke="var(--green)" stroke-width="4" stroke-linejoin="round">
      <path d="M22 24 H68"/>
      <path d="M32 24 V12 H58 V24"/>
      <path d="M33 28 V34 C33 42 38 48 45 48 C52 48 57 42 57 34 V28"/>
      <path d="M16 84 V68 C16 60 22 54 30 54 H60 C68 54 74 60 74 68 V84"/>
      <path d="M32 84 V64 H58 V84"/>
      <path d="M32 64 L28 54 M58 64 L62 54"/>
    </svg>
  </div><span class="num">01</span></div>
  <p>Register as an Aspiring<br>Farmer</p><span class="b">Register</span>
</div>
<div class="abs step" style="left:458px">
  <div class="ring"><div class="disc">
    <svg width="90" height="90" viewBox="0 0 90 90" role="img" aria-label="Handshake icon" fill="none" stroke="var(--green)" stroke-width="4" stroke-linejoin="round" stroke-linecap="round">
      <path d="M6 24 H20 L32 18 H48 L56 26"/>
      <path d="M84 24 H70 L60 30 H44 C40 30 40 36 44 36 H54"/>
      <path d="M20 24 V52 L34 62 C38 65 42 62 40 58"/>
      <path d="M34 62 L40 66 C44 68 47 64 45 61"/>
      <path d="M40 66 L46 70 C50 72 53 68 50 65"/>
      <path d="M70 24 V52 L58 62 C54 66 50 64 50 60"/>
      <path d="M14 80 C26 74 36 84 46 78 C56 72 66 82 78 76"/>
    </svg>
  </div><span class="num">02</span></div>
  <p>Build your farm skills to<br>get yourself farm-ready.</p><span class="b">Farm Ready</span>
</div>
<div class="abs step" style="left:744px">
  <div class="ring"><div class="disc">
    <svg width="90" height="90" viewBox="0 0 90 90" role="img" aria-label="Farmhouse and tree icon" fill="none" stroke="var(--green)" stroke-width="4" stroke-linejoin="round">
      <path d="M10 40 L36 14 L62 40"/>
      <path d="M16 34 V80 H56 V34"/>
      <path d="M28 80 V56 H44 V80"/>
      <path d="M28 56 L44 80 M44 56 L28 80"/>
      <rect x="30" y="36" width="12" height="10"/>
      <circle cx="70" cy="56" r="11"/>
      <path d="M70 67 V80"/>
      <path d="M6 80 H84"/>
    </svg>
  </div><span class="num">03</span></div>
  <p>Together we find you<br>your dream farm.</p><span class="b">Match Making</span>
</div>

<section class="abs testimonials" role="img" aria-label="Green-tinted photo of crop rows across rolling hills"></section>
<h2 class="abs testi-title">Testimonials</h2>
<div class="abs quote" style="left:197px">Neque porro quisquam est qui dolorem ipsum quia dolor sit amet, consectetur, Lorem Ipsum is simply dummy text of the printing and typesetting industry. Lorem Ipsum has been the industry's standard dummy text .</div>
<div class="abs quote" style="left:610px">Neque porro quisquam est qui dolorem ipsum quia dolor sit amet, consectetur, Lorem Ipsum is simply dummy text of the printing and typesetting industry. Lorem Ipsum has been the industry's standard dummy text .</div>
<div class="abs author" style="left:196px"><span class="avatar" role="img" aria-label="Customer portrait"></span>Maren</div>
<div class="abs author" style="left:604px"><span class="avatar" role="img" aria-label="Customer portrait"></span>Ezra</div>
<div class="abs tdots"><span></span><span></span><span></span></div>

<footer class="abs footer"></footer>
<div class="abs fcol" style="left:131px;top:2690px">
  <h4>Quick Links</h4>
  <ul class="links"><li>Farmers</li><li>Investors</li><li>Retiring</li><li>About</li><li>Pricing</li><li>Contact</li></ul>
</div>
<div class="abs fcol" style="left:346px;top:2690px">
  <h4>Newsletter</h4>
  <div class="email">Enter Email id</div>
  <span class="subscribe">Subscribe</span>
</div>
<div class="abs fcol" style="left:625px;top:2690px">
  <h4>Contact Us</h4>
  <ul class="contact">
    <li><svg width="12" height="16" viewBox="0 0 12 16"><path d="M6 0a6 6 0 0 0-6 6c0 4.5 6 10 6 10s6-5.5 6-10a6 6 0 0 0-6-6zm0 8.5A2.5 2.5 0 1 1 6 3.5a2.5 2.5 0 0 1 0 5z" fill="#333"/></svg><span>Unit 4 218 Wattle Creek Rd<br>North Ashby</span></li>
    <li><svg width="14" height="14" viewBox="0 0 14 14"><path d="M3 0l3 3-2 2c1 2 3 4 5 5l2-2 3 3-2 3C6 14 0 8 0 2z" fill="#333"/></svg><span>(555)-201-4830</span></li>
    <li><svg width="14" height="11" viewBox="0 0 14 11"><rect width="14" height="11" fill="#333"/><path d="M0 0l7 6 7-6" stroke="#fff" fill="none"/></svg><span>hello@meadowrunacres.example</span></li>
  </ul>
</div>
<div class="abs fcol" style="left:890px;top:2690px">
  <h4>Follow Us</h4>
  <div class="social"><span></span><span></span><span></span><span></span></div>
</div>
<div class="abs fbrand"><span class="dot"></span>Meadowrun Acres</div>
<div class="abs copyright">Copyrights © 2017, www.meadowrunacres.example. All Rights Reserved.</div>
</body>
</html>
```